Podiatry clinic requires a modern revamp and editing of existing website.

I would like a fresh new look and updated information for my current business website. An easy to navigate site with prominent address and phone number for call to action. We are a podiatry clinic that focuses on general and sports podiatry.
I would like 4 pages; including Home page, About Us, Services & Contact.
www.brambleridgepodiatry.net

Target Market(s)

Active working professionals.

Industry/Entity Type

Medical

Coding

Coded - Design and coding required

Number of Pages Required

4 page

Font styles to use
Sans Serif

Colors
6b449b

Requirements
Must have
• A modern look with logo and active images; clean and uncluttered. Visible phone number and address for call to action.
• 4 pages - Home, About Us, Services, Contact.
• Home page - update address & service logos.
• About Us - update of personal information.
• Services - Revamp of existing page.
• Contact page to include Google map, email & phone number.
Nice to have
• Ability to add content easily; eg. a blog or adding video onto Home page.
• Link to Facebook page.

```html
<!DOCTYPE html>
<html lang="en">
<head>
<meta charset="utf-8">
<title>Bramble Ridge Podiatry</title>
<link rel="stylesheet" href="https://fonts.googleapis.com/css2?family=Open+Sans:wght@400;600;700;800&display=swap">
<style>
:root{
  --header-bg:#9a86c3;
  --nav-top:#5b3fa4;
  --nav-bottom:#46318f;
  --brand-deep:#45318f;
  --brand-ink:#3d2b86;
  --accent:#f26a1b;
  --accent-green:#9ad14b;
  --text:#444;
  --muted:#555;
  --footer-bg:#f1f1f1;
  --bar-bg:#4b4b4b;
  --white:#fff;
}
*{box-sizing:border-box;margin:0;padding:0}
html,body{width:1200px;height:2195px;overflow:hidden}
body{font-family:"Open Sans",Arial,sans-serif;color:var(--text);background:var(--white)}
a{color:inherit;text-decoration:none}

.site-header{height:138px;background:var(--header-bg);position:relative}
.brand{position:absolute;left:76px;top:22px;display:flex;align-items:center;gap:12px}
.brand-dot{width:40px;height:40px;border-radius:50%;background:var(--brand-ink)}
.brand-name{font-size:22px;font-weight:700;line-height:1.05;color:var(--brand-ink)}
.header-contact{position:absolute;left:824px;top:40px;color:var(--white);font-size:15.5px;font-weight:600;line-height:33px}
.header-contact div{display:flex;align-items:center;gap:10px}
.header-contact svg{width:14px;height:14px;fill:var(--white)}

.main-nav{height:54px;background:linear-gradient(var(--nav-top),var(--nav-bottom));display:flex;align-items:center;padding-left:85px;gap:36px}
.main-nav a{color:var(--white);font-size:13px;font-weight:600;letter-spacing:.2px;text-transform:uppercase}
.main-nav a.is-active{color:var(--accent-green)}

.hero{height:467px;position:relative;background:linear-gradient(180deg,#6d7482 0%,#b8a898 45%,#c9a78c 70%,#6f8a3d 92%,#557a2c 100%);text-align:center;color:var(--white)}
.hero-title{position:absolute;top:88px;left:0;right:0;font-size:48px;font-weight:800;line-height:49px;letter-spacing:1px;text-transform:uppercase;text-shadow:0 2px 6px rgba(0,0,0,.35)}
.btn{display:inline-block;background:var(--accent);color:var(--white);font-weight:700;border-radius:20px;text-transform:uppercase}
.hero .btn{position:absolute;left:474px;top:254px;width:252px;height:38px;line-height:38px;font-size:14px;letter-spacing:.5px}
.hero-dots{position:absolute;top:601px;left:0}
.dots{position:absolute;top:409px;left:565px;display:flex;gap:7px}
.dots span{width:12px;height:12px;border-radius:50%;background:var(--white)}
.dots span:first-child{background:var(--accent)}

.welcome{height:321px;text-align:center;padding-top:47px}
.section-title{font-size:24px;font-weight:600;text-transform:uppercase;letter-spacing:.3px}
.welcome .section-title{color:var(--brand-ink)}
.welcome p{width:1030px;margin:18px auto 0;font-size:15px;line-height:26px;color:var(--muted)}
.welcome .cta{margin-top:24px;color:var(--accent);font-weight:600;font-size:16.5px;line-height:26px}

.services{height:681px;background:var(--brand-deep);color:var(--white);padding-top:47px}
.services .section-title{text-align:center}
.services .intro{width:1050px;margin:22px auto 0;text-align:center;font-size:15px;line-height:25px}
.service-grid{display:flex;gap:28px;margin:44px 0 0 76px}
.service-card{width:512px}
.service-photo{height:241px;background:linear-gradient(135deg,#e9ecef,#b9c3cc 60%,#dcd3c8)}
.service-card h3{margin-top:22px;font-size:18.5px;font-weight:700;color:var(--accent-green);letter-spacing:.4px}
.service-card p{margin-top:10px;font-size:15px;line-height:23.5px}
.service-card .btn{margin-top:22px;width:151px;height:38px;line-height:38px;text-align:center;font-size:14px}

.partners{height:183px;display:flex;gap:29px;padding:51px 0 0 76px}
.partner-badge{width:241px;height:93px;border:1px solid #cfcfcf;display:flex;align-items:center;justify-content:center}
.partner-badge span{width:150px;height:42px;border-radius:6px;background:#dcd6ea}

.site-footer{height:285px;background:var(--footer-bg);display:flex;padding:42px 0 0 76px}
.footer-col h4{font-size:15px;font-weight:700;color:var(--brand-ink);text-transform:uppercase;letter-spacing:.3px;margin-bottom:9px}
.quick-links{width:359px}
.quick-links li{list-style:none;font-size:13.5px;line-height:26.6px;color:var(--muted)}
.contact-col{width:358px;font-size:13.5px;color:var(--muted);line-height:23px}
.contact-col strong{display:block;font-weight:700;color:#333;text-transform:uppercase;margin-bottom:4px;font-size:13px}
.contact-col .line{display:flex;align-items:center;gap:10px;margin-top:9px}
.contact-col svg{width:12px;height:12px;fill:var(--brand-ink)}
.map-box{width:334px;height:178px;background:linear-gradient(135deg,#ece6dc,#e2ddd3 50%,#d5dbe2);border:1px solid #ccc;margin-top:4px}

.bottom-bar{height:66px;background:var(--bar-bg);display:flex;align-items:center;justify-content:space-between;padding:0 56px 0 76px;color:var(--white);font-size:11px}
.social{display:flex;gap:6px}
.social span{width:30px;height:30px;border-radius:50%;background:#7d7d7d}
</style>
</head>
<body>

<header class="site-header">
  <a class="brand" href="#">
    <span class="brand-dot"></span>
    <span class="brand-name">bramble ridge<br>podiatry</span>
  </a>
  <div class="header-contact">
    <div><svg viewBox="0 0 24 24"><path d="M6.6 10.8a15.1 15.1 0 0 0 6.6 6.6l2.2-2.2c.3-.3.7-.4 1-.2 1.1.4 2.3.6 3.6.6.6 0 1 .4 1 1V20c0 .6-.4 1-1 1C10.6 21 3 13.4 3 4c0-.6.4-1 1-1h3.5c.6 0 1 .4 1 1 0 1.3.2 2.5.6 3.6.1.3 0 .7-.2 1z"/></svg>Phone: 1300 555 019</div>
    <div><svg viewBox="0 0 24 24"><path d="M2 5h20v2l-10 6L2 7zm0 4 10 6 10-6v10H2z"/></svg>Email: info@brambleridgepodiatry.net</div>
  </div>
</header>

<nav class="main-nav">
  <a class="is-active" href="#">Home</a>
  <a href="#">About Us</a>
  <a href="#">Podiatry Treatments</a>
  <a href="#">Podiatry Products Footwear</a>
  <a href="#">Health &amp; Wellness Products</a>
  <a href="#">Links</a>
  <a href="#">Contact Us</a>
</nav>

<section class="hero" role="img" aria-label="Photo of three people sitting on grass with bare feet toward the camera">
  <h1 class="hero-title">We are a podiatry clinic<br>in Australia.</h1>
  <a class="btn" href="#">Book an appoint ment</a>
  <div class="dots"><span></span><span></span><span></span><span></span></div>
</section>

<section class="welcome">
  <h2 class="section-title">Welcome to our website</h2>
  <p>Bramble Ridge Podiatry is a Podiatry clinic in the heart of Melbourne CBD. We are located between Ferris &amp; Oakley Streets in the Harbourview Business Centre / Elmstead Hotel Complex. Our podiatrists are fully qualified health professionals who are able to diagnose, treat, manage or help to prevent all medical conditions that affect the feet and lower limb. We provide General Podiatry Treatment and some Specialised Services in relation to various foot conditions, including Sports Injuries, Orthotic Therapy and Nail Surgery.</p>
  <div class="cta">For Appointments or Enquiries please call us on 1300 555 019<br>or Email: &nbsp; info@brambleridgepodiatry.net</div>
</section>

<section class="services">
  <h2 class="section-title">Podiatry Services</h2>
  <p class="intro">Aliquam molestie, mi et imperdiet euismod, dui purus auctor tellus, et interdum lacus lectus et ante. Sed accumsan sollicitudin sapien, sit amet adipiscing turpis gravida ac. In congue, neque ac lobortis volutpat, libero mauris varius mi, vitae suscipit ipsum ligula vitae risus.</p>
  <div class="service-grid">
    <article class="service-card">
      <div class="service-photo" role="img" aria-label="Photo of a gloved practitioner examining a patient's foot"></div>
      <h3>General Treatments</h3>
      <p>Aliquam molestie, mi et imperdiet euismod, dui purus auctor tellus, et interdum lacus lectus et ante. Sed accumsan sollicitudin sapien, sit amet adipiscing turpis gravida ac.</p>
      <a class="btn" href="#">Read More</a>
    </article>
    <article class="service-card">
      <div class="service-photo" role="img" aria-label="Photo of a podiatrist using a magnifying lamp during a treatment"></div>
      <h3>Specialised Treatments</h3>
      <p>Aliquam molestie, mi et imperdiet euismod, dui purus auctor tellus, et interdum lacus lectus et ante. Sed accumsan sollicitudin sapien, sit amet adipiscing turpis gravida ac.</p>
      <a class="btn" href="#">Read More</a>
    </article>
  </div>
</section>

<section class="partners" aria-label="Partner and provider badges">
  <div class="partner-badge"><span></span></div>
  <div class="partner-badge"><span></span></div>
  <div class="partner-badge"><span></span></div>
  <div class="partner-badge"><span></span></div>
</section>

<footer class="site-footer">
  <div class="footer-col quick-links">
    <h4>Quick Links</h4>
    <ul>
      <li>Home</li><li>About us</li><li>Podiatry treatments</li><li>Podiatry Products Footwear</li><li>Health &amp; Wellness Products</li><li>Links</li><li>Contact Us</li>
    </ul>
  </div>
  <div class="footer-col contact-col">
    <h4>Contact Us</h4>
    <strong>Bramble Ridge Podiatry</strong>
    Suite 12/88 Ridgeway Street<br>Melbourne 3000
    <div class="line"><svg viewBox="0 0 24 24"><path d="M6.6 10.8a15.1 15.1 0 0 0 6.6 6.6l2.2-2.2c.3-.3.7-.4 1-.2 1.1.4 2.3.6 3.6.6.6 0 1 .4 1 1V20c0 .6-.4 1-1 1C10.6 21 3 13.4 3 4c0-.6.4-1 1-1h3.5c.6 0 1 .4 1 1 0 1.3.2 2.5.6 3.6.1.3 0 .7-.2 1z"/></svg>Phone: 1300 555 019</div>
    <div class="line"><svg viewBox="0 0 24 24"><path d="M2 5h20v2l-10 6L2 7zm0 4 10 6 10-6v10H2z"/></svg>Email: info@brambleridgepodiatry.net</div>
  </div>
  <div class="footer-col">
    <h4>Location Map</h4>
    <div class="map-box" role="img" aria-label="Street map showing the clinic location in Melbourne CBD"></div>
  </div>
</footer>

<div class="bottom-bar">
  <span>Copyright © 2016. Company Name. All Right Reserved</span>
  <div class="social" aria-label="Social links"><span></span><span></span><span></span><span></span><span></span><span></span></div>
</div>

</body>
</html>
```